New Business Card Design Project LORVANTI-Italy

we are LORVANTI-Italy
our company in the market for 3 years we are luxury cosmetic company and its about time for a facelift :)
i will like to have elegant luxurious and unique business card
that will give the person that get it a unique, luxurious and elegant impression
I'm VERY OPEN FOR NEW IDEAS , even duo i add a few files of things that i see on line and i like them

i add my logo as well
my website is LORVANTI.COM
(if you would like to see the main style that we have)

Target Market(s)

adult that have money :)

Industry/Entity Type

Business

Contact Information for Business Card

Name - Dario Lorvanti
Position - CEO and CO Founder
address - 4817 E Halvern
telephone - 555-384-1926
email - dario@lorvanti.com
fax - 555-384-1926
website - LORVANTI.COM

Colors
000000
959595
fbee3e
ffffff

Requirements
Must have
• big logo in GOLD color
• elegant look
• impressive
Nice to have
• not must but maybe classy pattern background
• not must but maybe emblem
• maybe clear plastic business card
Should not have
• colors
• images

```html
<!DOCTYPE html>
<html lang="en">
<head>
<meta charset="utf-8">
<title>LORVANTI-Italy Business Card</title>
<link rel="stylesheet" href="https://fonts.googleapis.com/css2?family=EB+Garamond:wght@400;500&display=swap">
<style>
  :root {
    --backdrop: #1b1b1b;
    --card: #121212;
    --card-edge: #2a2a2a;
    --gold: #d6ab3c;
    --white: #f4f4f4;
  }
  * { margin: 0; padding: 0; box-sizing: border-box; }
  html, body {
    width: 1200px;
    height: 833px;
    overflow: hidden;
    background: var(--backdrop);
  }
  .canvas {
    position: relative;
    width: 1200px;
    height: 833px;
    display: flex;
    align-items: center;
    justify-content: center;
    gap: 40px;
    font-family: "EB Garamond", Georgia, serif;
  }
  .card {
    position: relative;
    width: 520px;
    height: 297px;
    background: var(--card);
    border: 1px solid var(--card-edge);
    border-bottom: 4px solid var(--gold);
    border-radius: 3px;
  }

  /* Front */
  .front {
    display: flex;
    flex-direction: column;
    align-items: center;
    justify-content: center;
    gap: 18px;
  }
  .brand-mark {
    width: 92px;
    height: 92px;
    border: 3px solid var(--gold);
    border-radius: 50%;
  }
  .brand-name {
    color: var(--gold);
    font-size: 46px;
    font-weight: 400;
    letter-spacing: 2px;
    line-height: 1;
  }

  /* Back */
  .back { padding: 44px 0 0 44px; }
  .contact {
    color: var(--white);
    font-size: 17px;
    line-height: 1.2;
  }
  .contact .person-name {
    color: var(--gold);
    font-size: 23px;
    font-weight: 500;
  }
  .contact .company {
    color: var(--gold);
    font-size: 17px;
    font-weight: 500;
    margin-top: 10px;
  }
  .contact .lines { margin-top: 14px; list-style: none; }
  .contact .lines li {
    display: flex;
    align-items: center;
    gap: 8px;
  }
  .contact .lines svg {
    width: 14px;
    height: 14px;
    fill: none;
    stroke: var(--gold);
    stroke-width: 1.6;
    flex: none;
  }
  .back-brand {
    position: absolute;
    right: 40px;
    bottom: 36px;
    width: 200px;
    height: 200px;
    display: flex;
    align-items: center;
    justify-content: center;
    border: 3px solid var(--gold);
    border-radius: 50%;
  }
  .back-brand .brand-name { font-size: 30px; letter-spacing: 1px; }
</style>
</head>
<body>
<main class="canvas">

  <section class="card front" aria-label="Card front">
    <span class="brand-mark"></span>
    <span class="brand-name">LORVANTI</span>
  </section>

  <section class="card back" aria-label="Card back">
    <div class="contact">
      <p class="person-name">Dario Lorvanti</p>
      <p class="role">CEO and CO Founder</p>
      <p class="company">LORVANTI-Italy</p>
      <p class="address">4817 E Halvern</p>
      <ul class="lines">
        <li>
          <svg viewBox="0 0 16 16" aria-hidden="true"><path d="M3 2h3l1.5 3.5-2 1.2a8 8 0 0 0 3.8 3.8l1.2-2L14 10v3a1 1 0 0 1-1 1A11 11 0 0 1 2 3a1 1 0 0 1 1-1z"/></svg>
          <span>555-384-1926</span>
        </li>
        <li>
          <svg viewBox="0 0 16 16" aria-hidden="true"><rect x="2" y="6" width="12" height="7" rx="1"/><path d="M4.5 6V2.5h7V6M5 10h6"/></svg>
          <span>555-384-1926</span>
        </li>
        <li>
          <svg viewBox="0 0 16 16" aria-hidden="true"><rect x="2" y="4" width="12" height="8" rx="1"/><path d="M2 4.5l6 4.5 6-4.5"/></svg>
          <span>dario@lorvanti.com</span>
        </li>
        <li>
          <svg viewBox="0 0 16 16" aria-hidden="true"><circle cx="8" cy="8" r="6"/><path d="M2 8h12M8 2c2 2 2 10 0 12M8 2c-2 2-2 10 0 12"/></svg>
          <span>LORVANTI.COM</span>
        </li>
      </ul>
    </div>
    <div class="back-brand">
      <span class="brand-name">LORVANTI</span>
    </div>
  </section>

</main>
</body>
</html>
```